Trovanta Overview and Demo Presentation

Objective:
Create a bold, visually engaging PowerPoint deck to present Trovanta’s sales process and system demo to local movers, emphasizing ease of use, increased profitability, and operational efficiency.
Key Elements:
• Design: High-impact graphics with Trovanta branding, minimal text, and clean layouts.
• Content: Step-by-step sales process, key selling points, system demo walkthrough, and a compelling call-to-action.
• Live Demo: Showcase Trovanta’s platform, focusing on instant guaranteed pricing, streamlined booking, and support features.
Deliverables:
A dynamic presentation designed to educate and convert local movers into Trovanta partners, ensuring seamless flow and strong audience engagement.

Target Market(s)

Local Movers

Industry/Entity Type

Household Goods Moving

Font styles to use
Sans Serif

Colors
0054AA
0677BA
7BADD7
CADEEF
E8F1F8
FFC000
F8CF3A
FAE287
FDF2CF
FEFAEE

Requirements
Must have
• Project Brief: Trovanta Sales Process Presentation Objective: Create a bold, visually engaging PowerPoint deck to present Trovanta’s sales process and system demo to local movers, emphasizing ease of use, increased profitability, and operational efficiency. Key Elements: • Design: High-impact graphics with Trovanta branding, minimal text, and clean layouts. • Content: Step-by-step sales process, key selling points, system demo walkthrough, and a compelling call-to-action. • Live Demo: Showcase Trovanta’s platform, focusing on instant guaranteed pricing, streamlined booking, and support features. Deliverables: A dynamic presentation designed to educate and convert local movers into Trovanta partners, ensuring seamless flow and strong audience engagement.

```html
<!DOCTYPE html>
<html lang="en">
<head>
<meta charset="utf-8">
<title>Trovanta Partner Overview Presentation</title>
<link rel="stylesheet" href="https://fonts.googleapis.com/css2?family=Poppins:ital,wght@0,400;0,500;0,600;0,700;1,600&family=Roboto:ital,wght@0,400;0,500;0,700;1,700&display=swap">
<style>
:root{
  --blue-deep:#0054AA;
  --blue:#0677BA;
  --blue-mid:#7BADD7;
  --blue-soft:#CADEEF;
  --blue-pale:#E8F1F8;
  --gold:#FFC000;
  --gold-warm:#F8CF3A;
  --gold-soft:#FAE287;
  --gold-pale:#FDF2CF;
  --ink:#1b1b1b;
  --bar:#1f1f1f;
  --sheet:#ededed;
  --white:#ffffff;
}
*{box-sizing:border-box;margin:0;padding:0}
html,body{width:1105px;height:1200px;overflow:hidden;background:var(--sheet)}
body{position:relative;font-family:"Roboto",Arial,sans-serif;color:var(--ink)}
.slide{position:absolute;width:481px;height:270px;background:var(--white);overflow:hidden}
.col-a{left:48px}.col-b{left:577px}
.row-1{top:27px}.row-2{top:311px}.row-3{top:597px}.row-4{top:882px}
.abs{position:absolute}
.footer{position:absolute;left:0;bottom:0;width:100%;height:16px;background:var(--bar);display:flex;align-items:center;justify-content:space-between;padding:0 8px}
.footer .brand{font-family:"Poppins",sans-serif;font-weight:600;font-size:9px;color:var(--white);letter-spacing:.2px}
.footer .page{width:11px;height:11px;border-radius:50%;background:var(--white);color:var(--ink);font-size:6px;font-weight:700;display:flex;align-items:center;justify-content:center}
.title{font-family:"Poppins",sans-serif;font-weight:600;color:var(--blue-deep);text-align:center;line-height:1.1}
.badge{position:absolute;background:var(--gold-warm);color:#3a2a00;font-family:"Poppins",sans-serif;font-weight:600;font-size:10px;border-radius:4px;display:flex;align-items:center;justify-content:center;letter-spacing:.3px}
.body-text{font-size:6px;line-height:1.55;color:var(--ink)}
.photo{position:absolute}

/* slide 1 cover */
.cover-brand{left:10px;top:72px;font-family:"Poppins",sans-serif;font-weight:600;font-size:31px;color:var(--white);letter-spacing:.5px}
.cover-title{left:10px;top:120px;font-family:"Poppins",sans-serif;font-weight:700;font-size:20.5px;line-height:1.3;color:var(--white)}
.cover-sub{left:10px;top:178px;font-family:"Poppins",sans-serif;font-weight:500;font-size:10.5px;color:var(--white)}

/* slide 2 */
.stat-box{position:absolute;top:97px;width:173px;height:140px;border-radius:5px;color:var(--white);text-align:center}
.stat-box.blue{left:18px;background:var(--blue)}
.stat-box.gold{left:290px;background:var(--gold-warm)}
.stat-big{font-family:"Poppins",sans-serif;font-weight:700;font-size:19px;margin-top:6px;line-height:1.2}
.stat-label{font-size:8px;font-weight:500}
.stat-pill{width:60px;height:22px;margin:13px auto 13px;background:var(--white);color:var(--ink);border-radius:4px;font-size:8px;font-weight:500;display:flex;align-items:center;justify-content:center;position:relative}
.stat-pill::before,.stat-pill::after{content:"";position:absolute;left:50%;width:1px;height:8px;background:var(--white)}
.stat-pill::before{top:-10px}.stat-pill::after{bottom:-10px}
.proven{left:207px;top:149px;width:67px;height:35px;border:1px solid #bfc7cf;border-radius:4px;color:var(--blue);font-family:"Poppins",sans-serif;font-weight:600;font-size:9.5px;line-height:1.3;text-align:center;padding-top:3px}

/* slide 3 */
.dash{left:119px;top:63px;width:244px;height:125px;border:1px solid var(--blue-mid);border-radius:3px;background:#f6f7f9;overflow:hidden}
.dash-head{font-size:11px;color:#333;padding:2px 4px;display:flex;align-items:baseline;gap:3px}
.dash-head b{color:var(--blue);font-weight:500}
.dash-head small{font-size:4px;color:#2a8a3a}
.growth-card{position:absolute;top:196px;width:121px;height:52px;border-radius:4px;padding:5px 8px;background:var(--blue-soft);color:var(--ink)}
.growth-card.dark{background:var(--blue-deep);color:var(--white)}
.growth-card h3{font-family:"Poppins",sans-serif;font-weight:600;font-size:9.5px;line-height:1.15;color:var(--blue-deep)}
.growth-card.dark h3{color:var(--white)}
.growth-card p{font-size:6px;line-height:1.5;margin-top:3px}

/* slide 4 */
.value-card{position:absolute;top:92px;width:115px;height:125px;background:var(--white);border-radius:4px;text-align:center;padding-top:46px}
.value-card h3{font-family:"Poppins",sans-serif;font-weight:600;font-size:11.5px;line-height:1.25;color:var(--blue-deep)}
.value-card p{font-size:7px;line-height:1.55;margin-top:6px;padding:0 6px}
.icon-ring{position:absolute;left:38px;top:-17px;width:38px;height:38px;border-radius:50%;background:var(--blue-soft);display:flex;align-items:center;justify-content:center}
.icon-core{width:30px;height:30px;border-radius:50%;background:var(--gold-warm);display:flex;align-items:center;justify-content:center}

/* slide 5 */
.step-title{position:absolute;font-family:"Poppins",sans-serif;font-weight:600;font-size:8.5px;color:var(--blue-deep)}
.step-text{position:absolute;font-size:6.2px;line-height:1.55}

/* slide 6 */
.future-title{left:252px;top:98px;font-family:"Poppins",sans-serif;font-weight:600;font-size:18.5px;color:var(--blue-deep)}
.future-sub{left:252px;top:128px;font-family:"Roboto",sans-serif;font-style:italic;font-weight:700;font-size:8px;color:var(--gold);letter-spacing:.3px}
.future-copy{left:252px;top:143px;width:215px;font-size:7.5px;line-height:1.75}

/* slide 7 */
.wl-title{left:10px;top:27px;font-family:"Poppins",sans-serif;font-weight:600;font-size:19px;color:var(--blue-deep)}
.wl-title span{color:var(--gold)}
.wl-sub{left:11px;top:58px;width:200px;font-style:italic;font-weight:700;font-size:7.8px;line-height:1.2;color:var(--gold)}
.wl-copy{left:11px;top:90px;width:210px;font-size:6.6px;line-height:1.85}
.wl-brand{left:11px;top:215px;font-family:"Poppins",sans-serif;font-weight:600;font-size:10px;color:var(--blue)}
.screen{left:232px;top:33px;width:236px;height:140px;background:#1a1a1a;border-radius:5px 5px 0 0;padding:7px}
.screen-inner{position:relative;width:100%;height:100%;background:linear-gradient(135deg,#3b4550,#5a6470 60%,#48525c);color:var(--white);text-align:center}
.screen-nav{display:flex;justify-content:space-between;font-size:3px;padding:4px 8px;font-weight:700;letter-spacing:.2px}
.screen-hero{font-family:"Poppins",sans-serif;font-weight:700;font-size:9px;line-height:1.1;margin-top:26px}
.screen-lead{font-size:5.5px;line-height:1.2;margin-top:9px}
.screen-cta{display:flex;justify-content:center;margin-top:5px}
.screen-cta span{font-size:3.2px;font-weight:700;padding:4px 9px}
.bezel{left:232px;top:173px;width:236px;height:24px;background:#d9dadc;border-radius:0 0 5px 5px}

/* slide 8 */
.closing{background:linear-gradient(125deg,#F8B83A 0%,#E8B24A 30%,#9a9a7a 60%,#2f5da8 100%)}
.thanks-brand{left:14px;top:40px;font-family:"Poppins",sans-serif;font-weight:600;font-size:33px;color:var(--white);letter-spacing:.5px}
.thanks{left:14px;top:92px;font-family:"Poppins",sans-serif;font-weight:600;font-size:19px;color:var(--white)}
.contact{position:absolute;left:14px;display:flex;align-items:center;gap:8px;color:var(--white);font-size:7.5px;line-height:1.55}
.contact-icon{width:25px;height:25px;border-radius:50%;background:var(--blue-deep);display:flex;align-items:center;justify-content:center;flex:none}
</style>
</head>
<body>

<!-- 1 Cover -->
<section class="slide col-a row-1">
  <div class="photo" role="img" aria-label="Photo of a smiling couple looking at a phone among moving boxes" style="left:0;top:0;width:481px;height:270px;background:linear-gradient(120deg,#d9c4a8,#c9a67e 45%,#b07f58 75%,#e8dccb)"></div>
  <svg class="abs" style="left:0;top:0" width="481" height="270" viewBox="0 0 481 270">
    <polygon points="150,0 176,0 296,135 148,270 122,270 272,135" fill="var(--gold-warm)"/>
    <polygon points="140,0 154,0 282,135 132,270 118,270 266,135" fill="#6f8ea0"/>
    <defs><linearGradient id="coverBlue" x1="0" y1="0" x2="1" y2="1"><stop offset="0" stop-color="#0a5fb0"/><stop offset="1" stop-color="#0b79c2"/></linearGradient></defs>
    <polygon points="0,0 138,0 268,135 124,270 0,270" fill="url(#coverBlue)"/>
  </svg>
  <div class="abs cover-brand">Trovanta</div>
  <h1 class="abs cover-title">Moving For The Next<br>Generation</h1>
  <div class="abs cover-sub">Partner Overview Presentation</div>
</section>

<!-- 2 Revolutionizing -->
<section class="slide col-a row-2">
  <div class="badge" style="left:182px;top:10px;width:118px;height:24px">REVOLUTIONIZING</div>
  <h2 class="abs title" style="left:0;top:36px;width:481px;font-size:19px">The Moving Industry With Ai</h2>
  <p class="abs body-text" style="left:28px;top:64px;width:425px;text-align:center">Trovanta is transforming the $90-100B moving industry by leveraging AI, GPS, and automated compliance to deliver the first instant guaranteed pricing platform. We're cutting out inefficiencies and middlemen to improve costs and service quality.</p>
  <div class="stat-box blue">
    <div class="stat-big">$1.9M</div>
    <div class="stat-label">Revenue Successfully Raised</div>
    <div class="stat-pill">To Build</div>
    <div class="stat-big" style="margin-top:0">$5</div>
    <div class="stat-label">Appraised Tech Stack</div>
  </div>
  <div class="abs proven">PROVEN<br>MODEL</div>
  <div class="stat-box gold">
    <div class="stat-big">$500K</div>
    <div class="stat-label">Additional Raise</div>
    <div class="stat-pill">To Prove</div>
    <div class="stat-big" style="margin-top:0">B21</div>
    <div class="stat-label">Successful Model</div>
  </div>
  <footer class="footer"><span class="brand">Trovanta</span><span class="page">2</span></footer>
</section>

<!-- 3 Financial projections -->
<section class="slide col-a row-3">
  <div class="badge" style="left:179px;top:10px;width:125px;height:24px">VALUATION GROWTH</div>
  <h2 class="abs title" style="left:0;top:36px;width:481px;font-size:19px">Financial Projections <span style="font-size:15px;color:#333">(B2I, B2B, B2C)</span></h2>
  <div class="abs dash">
    <div class="dash-head">TRV <b>2245.72</b><small>+0.12</small></div>
    <svg width="244" height="104" viewBox="0 0 244 104">
      <rect x="4" y="0" width="50" height="4" fill="#d6dbe0"/>
      <rect x="100" y="0" width="45" height="4" fill="#d6dbe0"/>
      <rect x="0" y="8" width="244" height="4" fill="#e1e5ea"/>
      <text x="4" y="11" font-size="3" fill="#444">Symbol  Last  Chg  Vol  Bid  Offer</text>
      <g fill="#7f8a96">
        <rect x="4" y="15" width="120" height="1.5"/><rect x="4" y="19" width="120" height="1.5"/>
        <rect x="4" y="23" width="120" height="1.5"/><rect x="4" y="27" width="120" height="1.5"/>
      </g>
      <g fill="#c63a3a"><rect x="176" y="15" width="14" height="1.5"/><rect x="176" y="30" width="14" height="1.5"/><rect x="176" y="78" width="14" height="1.5"/><rect x="176" y="84" width="14" height="1.5"/></g>
      <g fill="#8a939d">
        <rect x="176" y="20" width="14" height="1.5"/><rect x="176" y="25" width="14" height="1.5"/><rect x="176" y="36" width="14" height="1.5"/><rect x="176" y="42" width="14" height="1.5"/><rect x="176" y="48" width="14" height="1.5"/><rect x="176" y="54" width="14" height="1.5"/><rect x="176" y="60" width="14" height="1.5"/><rect x="176" y="66" width="14" height="1.5"/><rect x="176" y="72" width="14" height="1.5"/><rect x="176" y="90" width="14" height="1.5"/>
        <rect x="200" y="15" width="40" height="78" fill="none" stroke="#d0d5da" stroke-width=".5"/>
      </g>
      <g fill="#d8dde2"><rect x="4" y="73" width="20" height="3"/><rect x="30" y="73" width="20" height="3"/><rect x="56" y="73" width="25" height="3"/><rect x="86" y="73" width="20" height="3"/></g>
      <g stroke="#cfd4d9" stroke-width=".4"><line x1="16" y1="82" x2="165" y2="82"/><line x1="16" y1="88" x2="165" y2="88"/><line x1="16" y1="94" x2="165" y2="94"/></g>
      <path d="M18 96 C40 92 55 98 75 92 S105 86 128 88 L128 98 L18 98Z" fill="var(--blue)"/>
      <rect x="0" y="100" width="244" height="4" fill="#3a4d63"/>
    </svg>
  </div>
  <div class="growth-card" style="left:47px"><h3>B2I Valuation<br>Growth</h3><p>Targeting 10% of local movers, leading to a $600M valuation.</p></div>
  <div class="growth-card dark" style="left:180px"><h3>B2I Valuation<br>Growth</h3><p>Targeting 2.5% of local Fortune 1000, resulting in a $100M valuation</p></div>
  <div class="growth-card" style="left:313px"><h3>B2I Valuation<br>Growth</h3><p>Trovanta valuation reached $1.8B</p></div>
  <footer class="footer"><span class="brand">Trovanta</span><span class="page">3</span></footer>
</section>

<!-- 4 Why it matters -->
<section class="slide col-a row-4">
  <div class="photo" role="img" aria-label="Dark photo of a warehouse and trees behind the cards" style="left:0;top:120px;width:481px;height:150px;background:linear-gradient(180deg,#1f3a35,#2b4650 50%,#1c2a33);clip-path:polygon(0 55%,28% 18%,50% 40%,72% 10%,100% 45%,100% 100%,0 100%)"></div>
  <h2 class="abs title" style="left:0;top:12px;width:481px;font-size:19px">Why Does Trovanta Matter?</h2>
  <p class="abs" style="left:0;top:38px;width:481px;text-align:center;font-size:7.2px;font-weight:500">Partner with Trovanta and elevate your moving business by expanding your reach and capabilities without the hassle.</p>
  <div class="value-card" style="left:33px">
    <div class="icon-ring"><div class="icon-core"><svg width="14" height="14" viewBox="0 0 16 16"><path d="M8 1 15 4.5 8 8 1 4.5Z M1 5.5 7.5 9v6L1 11.5Z M15 5.5 8.5 9v6l6.5-3.5Z" fill="#fff"/></svg></div></div>
    <h3>Maximize<br>Opportunities</h3><p>Never miss out on another long distance move opportunity again.</p>
  </div>
  <div class="value-card" style="left:184px">
    <div class="icon-ring"><div class="icon-core"><span style="font-family:Poppins,sans-serif;font-weight:700;color:#fff;font-size:17px">$</span></div></div>
    <h3>Efficient<br>Pricing</h3><p>Easily quote competitive pricing and maintain desired profit margins.</p>
  </div>
  <div class="value-card" style="left:334px">
    <div class="icon-ring"><div class="icon-core"><svg width="14" height="14" viewBox="0 0 16 16"><rect x="1" y="3" width="14" height="12" rx="1.5" fill="#fff"/><rect x="4" y="1" width="2" height="4" fill="#fff"/><rect x="10" y="1" width="2" height="4" fill="#fff"/><g fill="var(--gold-warm)"><rect x="3" y="7" width="2" height="2"/><rect x="7" y="7" width="2" height="2"/><rect x="11" y="7" width="2" height="2"/><rect x="3" y="11" width="2" height="2"/><rect x="7" y="11" width="2" height="2"/><rect x="11" y="11" width="2" height="2"/></g></svg></div></div>
    <h3>Hassle-Free<br>Management</h3><p>Schedule, pay and track moves all through <b>Trovanta</b></p>
  </div>
  <footer class="footer"><span class="brand">Trovanta</span><span class="page">4</span></footer>
</section>

<!-- 5 How it works -->
<section class="slide col-b row-1">
  <h2 class="abs title" style="left:0;top:8px;width:481px;font-size:19px">How It Works</h2>
  <p class="abs" style="left:0;top:35px;width:481px;text-align:center;font-size:7px;font-weight:700">Trovanta is a tech-driven moving company that automates the move management process.</p>
  <svg class="abs" style="left:0;top:0" width="481" height="254" viewBox="0 0 481 254">
    <path d="M61 243 C85 250 108 240 115 229 C130 210 140 190 151 166 C165 140 185 125 212 121 C240 120 255 150 250 175 C245 205 205 200 200 170 C196 145 230 135 245 160 C260 185 300 200 350 169 C365 150 368 120 362 100 C345 75 300 85 305 120 C330 150 380 115 402 92" fill="none" stroke="#222" stroke-width="1" stroke-dasharray="1 2.2" stroke-linecap="round"/>
    <circle cx="61" cy="243" r="1.6" fill="#222"/>
    <g font-family="Poppins,sans-serif" font-weight="600" font-size="8" fill="#fff" text-anchor="middle">
      <g><circle cx="115" cy="229" r="11" fill="var(--gold-soft)"/><circle cx="115" cy="229" r="8" fill="var(--blue-deep)"/><text x="115" y="232">1</text></g>
      <g><circle cx="151" cy="166" r="11" fill="var(--gold-soft)"/><circle cx="151" cy="166" r="8" fill="var(--blue-deep)"/><text x="151" y="169">2</text></g>
      <g><circle cx="212" cy="121" r="11" fill="var(--gold-soft)"/><circle cx="212" cy="121" r="8" fill="var(--blue-deep)"/><text x="212" y="124">3</text></g>
      <g><circle cx="231" cy="196" r="11" fill="var(--gold-soft)"/><circle cx="231" cy="196" r="8" fill="var(--blue-deep)"/><text x="231" y="199">4</text></g>
      <g><circle cx="350" cy="169" r="11" fill="var(--gold-soft)"/><circle cx="350" cy="169" r="8" fill="var(--blue-deep)"/><text x="350" y="172">5</text></g>
      <g><circle cx="321" cy="78" r="11" fill="var(--gold-soft)"/><circle cx="321" cy="78" r="8" fill="var(--blue-deep)"/><text x="321" y="81">6</text></g>
    </g>
  </svg>
  <div class="step-title" style="left:30px;top:182px;width:113px;text-align:right">Spot An Opportunity</div>
  <div class="step-text" style="left:10px;top:194px;width:113px;text-align:right">Do not let a long-distance move prospect slip away.</div>
  <div class="step-title" style="left:60px;top:141px;width:77px;text-align:right">Get a Quote</div>
  <div class="step-text" style="left:10px;top:153px;width:137px;text-align:right">Quickly input details on <span style="color:var(--blue)">trovanta.com.</span></div>
  <div class="step-title" style="left:100px;top:84px;width:100px;text-align:right">Set your Price</div>
  <div class="step-text" style="left:60px;top:96px;width:140px;text-align:right">Offer a suitable price to your customer and secure a deal</div>
  <div class="step-title" style="left:216px;top:209px">Seamless Scheduling</div>
  <div class="step-text" style="left:216px;top:221px;width:220px">Use trovanta.com to schedule the service. Just pay the deposit and leave the rest to us. You can even take advantage of our move concierge if that is easier.</div>
  <div class="step-title" style="left:369px;top:153px">Stay Informed</div>
  <div class="step-text" style="left:369px;top:165px;width:95px">We ensure constant communication so you can update your customers at every step.</div>
  <div class="step-title" style="left:355px;top:49px">Flexible PricingStructure</div>
  <div class="step-text" style="left:355px;top:61px;width:120px">You decide the charges.We only bill you., letting you keep your desired profit.</div>
  <footer class="footer"><span class="brand">Trovanta</span><span class="page">5</span></footer>
</section>

<!-- 6 Future of moving -->
<section class="slide col-b row-2">
  <div class="photo" role="img" aria-label="Photo of a couple taping and packing cardboard moving boxes at home" style="left:0;top:0;width:245px;height:254px;background:linear-gradient(135deg,#e9e3da,#cdb597 45%,#a98357 75%,#6f5a44);clip-path:polygon(0 0,100% 0,77% 100%,0 100%)"></div>
  <svg class="abs" style="left:0;top:0" width="481" height="254" viewBox="0 0 481 254"><polygon points="236,60 240,60 200,233 196,233" fill="var(--gold-warm)"/></svg>
  <div class="badge" style="left:252px;top:73px;width:62px;height:24px">TROVANTA</div>
  <h2 class="abs future-title">The Future Of Moving</h2>
  <div class="abs future-sub">CUTTING OUT MIDDLEMEN</div>
  <p class="abs future-copy">Trovanta's direct-to-consumer model eliminates van lines, agents, &amp; brokers. Customers connect directly with professional movers, reducing layers of markup and ensuring clarity.</p>
  <footer class="footer"><span class="brand">Trovanta</span><span class="page">6</span></footer>
</section>

<!-- 7 White label -->
<section class="slide col-b row-3">
  <h2 class="abs wl-title"><span>Trovanta</span> White Label</h2>
  <p class="abs wl-sub">Partner with Trovanta and take advantage of our cutting-edge technology to gain a competitive edge in the industry</p>
  <p class="abs wl-copy">Trovanta offers a white labeling solution for companies looking to capture direct moves. Our technology platform can be customized with your branding to provide a seamless integration with your existing systems and processes. This allows you to offer a top-notch interstate moving experience to your customers, while leveraging the power of Trovanta's proven technology. With this solution, you can streamline your operations, increase customer satisfaction, and capture more business in the lucrative long-distance move market.</p>
  <div class="abs wl-brand">Trovanta</div>
  <div class="abs screen">
    <div class="screen-inner" role="img" aria-label="Website hero with a blurred photo of movers in the background">
      <div class="screen-nav"><span>HOME &nbsp;HOW WORKS &nbsp;SERVICES &nbsp;RESOURCES</span><span>Trovanta</span><span>ABOUT US &nbsp;CONTACT US &nbsp;TRACK MY MOVE</span></div>
      <div class="screen-hero">THE EFFORTLESS, STRESS<br>FREE MOVING SOLUTION</div>
      <div class="screen-lead">Experience The Fastest, Most<br>Streamlined Way To Move!</div>
      <div class="screen-cta"><span style="background:var(--gold-warm);color:#222">CORPORATE MOVE</span><span style="background:var(--blue);color:#fff">PERSONAL MOVE</span></div>
    </div>
  </div>
  <div class="abs bezel"></div>
  <svg class="abs" style="left:232px;top:197px" width="236" height="40" viewBox="0 0 236 40"><polygon points="100,0 136,0 140,28 96,28" fill="#c9cacc"/><rect x="82" y="28" width="72" height="4" rx="2" fill="#bdbec0"/><ellipse cx="118" cy="16" rx="100" ry="3" fill="#e4e4e4"/></svg>
  <footer class="footer"><span class="brand">Trovanta</span><span class="page">7</span></footer>
</section>

<!-- 8 Thank you -->
<section class="slide col-b row-4 closing">
  <div class="photo" role="img" aria-label="Photo of two smiling movers in uniforms carrying a box and a potted plant" style="left:236px;top:31px;width:245px;height:220px;border-radius:110px 0 0 110px;background:linear-gradient(135deg,#e6e4df,#c8c6c0 40%,#8f99b8 70%,#b08455)"></div>
  <div class="abs thanks-brand">Trovanta</div>
  <div class="abs thanks">Thank You</div>
  <div class="contact" style="top:122px">
    <span class="contact-icon"><svg width="10" height="10" viewBox="0 0 12 12"><path d="M6 0.5C3.8 0.5 2.2 2.2 2.2 4.3 2.2 7.2 6 11.5 6 11.5S9.8 7.2 9.8 4.3C9.8 2.2 8.2 0.5 6 0.5Zm0 5.3a1.5 1.5 0 1 1 0-3 1.5 1.5 0 0 1 0 3Z" fill="#fff"/></svg></span>
    <span>480 Harbor Line Rd., Suite 12<br>Riverton, OK 73000</span>
  </div>
  <div class="contact" style="top:162px">
    <span class="contact-icon"><svg width="10" height="10" viewBox="0 0 12 12"><path d="M3 0.8 4.8 3.4 3.7 4.8C4.4 6.4 5.6 7.6 7.2 8.3L8.6 7.2 11.2 9 10.2 11C5.2 10.8 1.2 6.8 1 1.8Z" fill="#fff"/></svg></span>
    <span>(800) 555-0147</span>
  </div>
  <div class="contact" style="top:199px">
    <span class="contact-icon"><svg width="10" height="10" viewBox="0 0 12 12"><rect x="1" y="2.5" width="10" height="7" rx="1" fill="#fff"/><path d="M1.5 3 6 6.5 10.5 3" fill="none" stroke="var(--blue-deep)" stroke-width="1"/></svg></span>
    <span>trovanta.com<br>support@trovanta.com</span>
  </div>
  <footer class="footer"><span class="brand">Trovanta</span><span class="page">8</span></footer>
</section>

</body>
</html>
```